Redesign Craft Brewing Recipe Website

Originally built with Bootstrap just to get the site going, I am seeking a complete redesign of the sites home page and recipe page. I am an experienced web developer with no graphic background, initially just looking for psd mocks.

I prefer styles that are clean and modern, and would prefer anything that is fun, engaging, and has an organic feel to it. I currently have a cartoon rabbit as a logo, but it needs some modification/tweaking, so any help in that area would be great as well.

Current site:
http://velvetfinch.cloudpagehost.net/

Current launch page/logo:
http://www.velvetfinch.com/

I like the overall layout of the elements currently, but the design sucks.

The launch page is at the following URL

Reason: Still looking for a more modern design. Designs received so far are too similar to the original.

My site is content based and does not contain images or products. Your design should not consist of large images.

Reason: The website has very little images, so the designs need to be more text and content based. The header needs to be very small and should not contain an ad rotater.

Target Market(s)

Home brewers, Craft brewers, Microbreweries, Brewpubs

Requirements
Must have
• Web 2.0 Look and Feel, Fun, Hip, Focus on content
Should not have
• A large photo as a header

```html
<!DOCTYPE html>
<html lang="en">
<head>
<meta charset="utf-8">
<title>Velvetfinch – Craft Beer Recipes</title>
<link rel="stylesheet" href="https://fonts.googleapis.com/css2?family=Mulish:ital,wght@0,400;0,600;0,800;1,400&family=Oswald:wght@500&display=swap">
<style>
:root{
  --wood-dark:#3a1d10;
  --wood-mid:#6a3519;
  --wood-light:#7d4220;
  --cream:#efe7dd;
  --paper:#e2ded7;
  --card:#ffffff;
  --ink:#333333;
  --muted:#8a8a8a;
  --accent:#c0603a;
  --extract:#c4271b;
  --partial:#e07f12;
  --allgrain:#1a9ad6;
  --srm-red:#b3311d;
  --srm-teal:#2a8f8a;
  --srm-green:#64a51b;
  --srm-blue:#1f7fc4;
  --cell:#e9e9e9;
  --social:#3b7fc4;
}
*{box-sizing:border-box;margin:0;padding:0}
html,body{width:697px;height:1200px;overflow:hidden}
body{font-family:"Mulish",Arial,sans-serif;color:var(--ink);background:var(--paper);position:relative}

/* header */
.site-header{position:absolute;left:0;top:0;width:697px;height:120px;
  background:linear-gradient(90deg,var(--wood-dark),var(--wood-mid) 25%,var(--wood-light) 50%,var(--wood-mid) 75%,var(--wood-dark))}
.topbar{position:absolute;left:0;top:0;width:697px;height:16px;background:rgba(30,12,4,.75)}
.search{position:absolute;left:82px;top:1px;width:116px;height:14px;background:#fff;border-radius:2px;font-size:7px;color:#888;padding:2px 4px}
.search svg{position:absolute;right:3px;top:3px}
.main-nav{position:absolute;right:52px;top:3px;display:flex;gap:22px;font-size:8px;color:#fff;white-space:nowrap}
.brand{position:absolute;left:0;right:0;top:64px;display:flex;justify-content:center;align-items:center;gap:8px}
.brand-dot{width:22px;height:22px;border-radius:50%;background:var(--cream)}
.brand-name{font-weight:800;font-size:26px;letter-spacing:1px;color:var(--cream)}

.tagline-bar{position:absolute;left:0;top:120px;width:697px;height:26px;background:var(--cream);font-size:9px;color:#333}
.tagline{position:absolute;right:202px;top:8px;white-space:nowrap}
.share{position:absolute;left:510px;top:7px;display:flex;gap:3px}
.share span{font-size:6px;border:1px solid #bbb;background:#f6f6f6;padding:1px 3px;border-radius:2px;white-space:nowrap}
.social-mini{position:absolute;left:588px;top:8px;display:flex;gap:6px}
.social-mini i{width:10px;height:10px;border-radius:50%;background:#a99;display:block}

.filter-bar{position:absolute;left:0;top:146px;width:697px;height:34px;background:#fbfaf8;border-bottom:2px dotted #d6d1c9}
.dropdown{position:absolute;top:6px;height:20px;background:#e4e1dc;border-radius:2px;font-size:8px;padding:5px 8px;color:#444;white-space:nowrap}
.dropdown::after{content:"";position:absolute;right:7px;top:9px;border:4px solid transparent;border-top-color:#888}
.sort{position:absolute;left:525px;top:6px;width:90px;height:20px;background:#fff;border:1px solid #ddd;border-radius:2px;font-size:8px;padding:4px 6px;white-space:nowrap}
.sort b{color:var(--extract);font-weight:400}
.sort i{display:inline-block;margin-left:3px;border:3px solid transparent;border-top-color:var(--extract);vertical-align:-1px}

/* cards */
.recipe-grid{position:absolute;left:84px;top:195px;display:grid;grid-template-columns:repeat(4,124px);grid-auto-rows:213px;column-gap:11px;row-gap:11px}
.recipe-card{background:var(--card);box-shadow:0 1px 3px rgba(0,0,0,.35);position:relative}
.photo{position:absolute;left:6px;top:5px;width:112px;height:112px}
.photo-title{position:absolute;left:6px;top:95px;width:112px;height:20px;background:rgba(20,10,5,.6);color:#fff;font-size:7.5px;text-align:center;padding-top:5px;white-space:nowrap}
.votes{position:absolute;left:6px;top:124px;display:flex;gap:2px}
.vote{width:12px;text-align:center;font-size:6px;color:#666}
.vote div{height:12px;background:#e7e7e7;display:flex;align-items:center;justify-content:center;margin-bottom:1px}
.method{position:absolute;right:6px;top:120px;color:#fff;font-size:6.5px;padding:1px 3px 1px 7px;white-space:nowrap;clip-path:polygon(6px 0,100% 0,100% 100%,6px 100%,0 50%)}
.method.extract{background:var(--extract)}
.method.partial{background:var(--partial)}
.method.allgrain{background:var(--allgrain)}
.style{position:absolute;right:6px;top:132px;font-size:6.5px;color:var(--muted);white-space:nowrap}
.desc{position:absolute;left:6px;top:150px;width:112px;font-size:6.8px;line-height:10px;color:#444}
.author{position:absolute;left:6px;top:173px;font-size:6.8px;color:#555;white-space:nowrap}
.author span{color:var(--accent)}
.stats{position:absolute;left:1px;top:188px;display:flex;gap:1px}
.stat{width:24px;height:22px;background:var(--cell);border:1px solid #cfcfcf;font-size:6.5px;text-align:center;line-height:9px;padding-top:2px;color:#333}
.stat.srm{color:#fff;border-color:transparent}
.srm.red{background:var(--srm-red)}.srm.teal{background:var(--srm-teal)}.srm.green{background:var(--srm-green)}.srm.blue{background:var(--srm-blue)}

/* footer */
.footer-band{position:absolute;left:0;top:1130px;width:697px;height:20px;background:linear-gradient(90deg,var(--wood-dark),var(--wood-light) 50%,var(--wood-dark))}
.footer-brand{position:absolute;left:0;right:0;top:1112px;display:flex;justify-content:center;align-items:center;gap:5px}
.footer-brand .brand-dot{width:14px;height:14px;background:var(--accent)}
.footer-brand .brand-name{font-size:15px;color:var(--accent)}
.footer-photo{position:absolute;left:532px;top:1088px;width:74px;height:58px;border-radius:10px;background:linear-gradient(90deg,#7a3410,#d98a2a 35%,#e8a040 60%,#8a3d12)}
.mailing{position:absolute;left:84px;top:1152px;width:529px;height:28px;background:#fff;display:flex;align-items:center;padding:0 5px;white-space:nowrap}
.mailing h2{font-family:"Oswald",Arial,sans-serif;font-weight:500;font-size:13px;color:var(--extract);letter-spacing:.2px;white-space:nowrap;flex:none}
.mailing p{font-size:7px;color:#444;margin-left:8px;flex:none}
.email{position:relative;width:98px;height:14px;border:1px solid #ccc;border-radius:8px;font-size:6.5px;color:#777;padding:2px 6px;margin-left:6px;flex:none}
.email b{position:absolute;right:-2px;top:-1px;width:22px;height:14px;border-radius:7px;background:var(--partial);color:#fff;font-size:6px;text-align:center;padding-top:3px}
.connect{font-size:7px;font-style:italic;color:#444;margin-left:5px;flex:none}
.social{display:flex;gap:3px;margin-left:5px;flex:none}
.social i{display:block;width:13px;height:13px;background:var(--social)}
.copyright{position:absolute;left:0;right:0;top:1186px;text-align:center;font-size:7px;color:#8a4a2a}
</style>
</head>
<body>

<header class="site-header">
  <div class="topbar">
    <div class="search">Search
      <svg width="8" height="8" viewBox="0 0 8 8"><circle cx="3.2" cy="3.2" r="2.3" fill="none" stroke="#333" stroke-width="1.1"/><line x1="5" y1="5" x2="7.5" y2="7.5" stroke="#333" stroke-width="1.2"/></svg>
    </div>
    <nav class="main-nav"><span>Recipes</span><span>About ▾</span><span>Login</span></nav>
  </div>
  <div class="brand"><span class="brand-dot"></span><span class="brand-name">VELVETFINCH</span></div>
</header>

<div class="tagline-bar">
  <p class="tagline">Velvetfinch is the easiest way to create and share craft beer recipes.</p>
  <div class="share"><span>Like 0</span><span>Send</span></div>
  <div class="social-mini"><i></i><i></i></div>
</div>

<div class="filter-bar">
  <div class="dropdown" style="left:82px;width:73px">Brewing</div>
  <div class="dropdown" style="left:161px;width:73px">Styles</div>
  <div class="dropdown" style="left:240px;width:73px">Match Maker</div>
  <div class="sort">Sort by <b>› Trending</b><i></i></div>
</div>

<main class="recipe-grid">
<article class="recipe-card"><div class="photo" role="img" aria-label="Beer being poured into a glass" style="background:linear-gradient(135deg,#5a6b1e,#e2b640 50%,#f3e3a0)"></div><div class="photo-title">Oak Bastard Sweet Mead</div><div class="votes"><div class="vote"><div>♥</div>10</div><div class="vote"><div>✔</div>9</div><div class="vote"><div>★</div>0</div></div><span class="method extract">Extract</span><span class="style">Belgian Tripel</span><p class="desc">Lorem ipsum dolor sit amet, consectetur adipisicing elit.</p><p class="author">Created by <span>Nora Hale</span></p><div class="stats"><div class="stat">2.24%<br>ABV</div><div class="stat">24<br>IBU</div><div class="stat">1.006<br>FG</div><div class="stat">1.022<br>OG</div><div class="stat srm red">4<br>SRM</div></div></article>

<article class="recipe-card"><div class="photo" role="img" aria-label="Beer glasses beside a barrel" style="background:linear-gradient(135deg,#1c120a,#6b4a22 55%,#d9a14a)"></div><div class="photo-title">Oak Bastard Sweet Mead</div><div class="votes"><div class="vote"><div>♥</div>8</div><div class="vote"><div>✔</div>15</div><div class="vote"><div>★</div>0</div></div><span class="method partial">PartialMash</span><span class="style">Mild</span><p class="desc">Lorem ipsum dolor sit amet, consectetur adipisicing elit.</p><p class="author">Created by <span>Nora Hale</span></p><div class="stats"><div class="stat">2.24%<br>ABV</div><div class="stat">24<br>IBU</div><div class="stat">1.006<br>FG</div><div class="stat">1.022<br>OG</div><div class="stat srm teal">4<br>SRM</div></div></article>

<article class="recipe-card"><div class="photo" role="img" aria-label="Two pints of amber beer in a pub" style="background:linear-gradient(135deg,#1a0c06,#a4381a 50%,#e59a3a)"></div><div class="photo-title">Oak Bastard Sweet Mead</div><div class="votes"><div class="vote"><div>♥</div>6</div><div class="vote"><div>✔</div>3</div><div class="vote"><div>★</div>0</div></div><span class="method allgrain">AllGrain</span><span class="style">Belgian Tripel</span><p class="desc">Lorem ipsum dolor sit amet, consectetur adipisicing elit.</p><p class="author">Created by <span>Nora Hale</span></p><div class="stats"><div class="stat">2.24%<br>ABV</div><div class="stat">24<br>IBU</div><div class="stat">1.006<br>FG</div><div class="stat">1.022<br>OG</div><div class="stat srm green">4<br>SRM</div></div></article>

<article class="recipe-card"><div class="photo" role="img" aria-label="Foamy pint of amber beer" style="background:linear-gradient(160deg,#2a1208,#c25a1c 55%,#f0b060)"></div><div class="photo-title">Oak Bastard Sweet Mead</div><div class="votes"><div class="vote"><div>♥</div>2</div><div class="vote"><div>✔</div>9</div><div class="vote"><div>★</div>0</div></div><span class="method extract">Extract</span><span class="style">Belgian Tripel</span><p class="desc">Lorem ipsum dolor sit amet, consectetur adipisicing elit.</p><p class="author">Created by <span>Nora Hale</span></p><div class="stats"><div class="stat">2.24%<br>ABV</div><div class="stat">24<br>IBU</div><div class="stat">1.006<br>FG</div><div class="stat">1.022<br>OG</div><div class="stat srm blue">4<br>SRM</div></div></article>

<article class="recipe-card"><div class="photo" role="img" aria-label="Beer glasses with a keg and wheat" style="background:linear-gradient(135deg,#f4efe6,#d89a3e 55%,#7a4718)"></div><div class="photo-title">Oak Bastard Sweet Mead</div><div class="votes"><div class="vote"><div>♥</div>5</div><div class="vote"><div>✔</div>20</div><div class="vote"><div>★</div>0</div></div><span class="method allgrain">AllGrain</span><span class="style">Belgian Tripel</span><p class="desc">Lorem ipsum dolor sit amet, consectetur adipisicing elit.</p><p class="author">Created by <span>Nora Hale</span></p><div class="stats"><div class="stat">2.24%<br>ABV</div><div class="stat">24<br>IBU</div><div class="stat">1.006<br>FG</div><div class="stat">1.022<br>OG</div><div class="stat srm blue">4<br>SRM</div></div></article>

<article class="recipe-card"><div class="photo" role="img" aria-label="Pints of beer with warm lights" style="background:linear-gradient(135deg,#3a1206,#b8561c 50%,#e8a040)"></div><div class="photo-title">Oak Bastard Sweet Mead</div><div class="votes"><div class="vote"><div>♥</div>0</div><div class="vote"><div>✔</div>6</div><div class="vote"><div>★</div>0</div></div><span class="method extract">Extract</span><span class="style">Munich Helles</span><p class="desc">Lorem ipsum dolor sit amet, consectetur adipisicing elit.</p><p class="author">Created by <span>Nora Hale</span></p><div class="stats"><div class="stat">2.24%<br>ABV</div><div class="stat">24<br>IBU</div><div class="stat">1.006<br>FG</div><div class="stat">1.022<br>OG</div><div class="stat srm red">4<br>SRM</div></div></article>

<article class="recipe-card"><div class="photo" role="img" aria-label="Beer pouring into a glass on green" style="background:linear-gradient(160deg,#8fa02a,#d8cf6a 50%,#e0a83a)"></div><div class="photo-title">Oak Bastard Sweet Mead</div><div class="votes"><div class="vote"><div>♥</div>3</div><div class="vote"><div>✔</div>8</div><div class="vote"><div>★</div>0</div></div><span class="method partial">PartialMash</span><span class="style">Mild</span><p class="desc">Lorem ipsum dolor sit amet, consectetur adipisicing elit.</p><p class="author">Created by <span>Nora Hale</span></p><div class="stats"><div class="stat">2.24%<br>ABV</div><div class="stat">24<br>IBU</div><div class="stat">1.006<br>FG</div><div class="stat">1.022<br>OG</div><div class="stat srm teal">4<br>SRM</div></div></article>

<article class="recipe-card"><div class="photo" role="img" aria-label="Beer mugs on a wooden table" style="background:linear-gradient(135deg,#4a2a10,#c88a3a 55%,#f2d08a)"></div><div class="photo-title">Oak Bastard Sweet Mead</div><div class="votes"><div class="vote"><div>♥</div>2</div><div class="vote"><div>✔</div>10</div><div class="vote"><div>★</div>0</div></div><span class="method allgrain">AllGrain</span><span class="style">Belgian Tripel</span><p class="desc">Lorem ipsum dolor sit amet, consectetur adipisicing elit.</p><p class="author">Created by <span>Nora Hale</span></p><div class="stats"><div class="stat">2.24%<br>ABV</div><div class="stat">24<br>IBU</div><div class="stat">1.006<br>FG</div><div class="stat">1.022<br>OG</div><div class="stat srm green">4<br>SRM</div></div></article>

<article class="recipe-card"><div class="photo" role="img" aria-label="Close-up pint of amber beer" style="background:linear-gradient(160deg,#f1ebe4,#c66a1c 45%,#7a2c0c)"></div><div class="photo-title">Oak Bastard Sweet Mead</div><div class="votes"><div class="vote"><div>♥</div>6</div><div class="vote"><div>✔</div>7</div><div class="vote"><div>★</div>0</div></div><span class="method partial">PartialMash</span><span class="style">Mild</span><p class="desc">Lorem ipsum dolor sit amet, consectetur adipisicing elit.</p><p class="author">Created by <span>Nora Hale</span></p><div class="stats"><div class="stat">2.24%<br>ABV</div><div class="stat">24<br>IBU</div><div class="stat">1.006<br>FG</div><div class="stat">1.022<br>OG</div><div class="stat srm teal">4<br>SRM</div></div></article>

<article class="recipe-card"><div class="photo" role="img" aria-label="Beer mug on a dark background" style="background:linear-gradient(135deg,#120804,#8a4a14 55%,#e2a040)"></div><div class="photo-title">Oak Bastard Sweet Mead</div><div class="votes"><div class="vote"><div>♥</div>5</div><div class="vote"><div>✔</div>7</div><div class="vote"><div>★</div>0</div></div><span class="method allgrain">AllGrain</span><span class="style">English Cider</span><p class="desc">Lorem ipsum dolor sit amet, consectetur adipisicing elit.</p><p class="author">Created by <span>Nora Hale</span></p><div class="stats"><div class="stat">2.24%<br>ABV</div><div class="stat">24<br>IBU</div><div class="stat">1.006<br>FG</div><div class="stat">1.022<br>OG</div><div class="stat srm blue">4<br>SRM</div></div></article>

<article class="recipe-card"><div class="photo" role="img" aria-label="Two pints of amber beer in a pub" style="background:linear-gradient(135deg,#1a0c06,#a4381a 50%,#e59a3a)"></div><div class="photo-title">Oak Bastard Sweet Mead</div><div class="votes"><div class="vote"><div>♥</div>4</div><div class="vote"><div>✔</div>3</div><div class="vote"><div>★</div>0</div></div><span class="method extract">Extract</span><span class="style">Belgian Tripel</span><p class="desc">Lorem ipsum dolor sit amet, consectetur adipisicing elit.</p><p class="author">Created by <span>Nora Hale</span></p><div class="stats"><div class="stat">2.24%<br>ABV</div><div class="stat">24<br>IBU</div><div class="stat">1.006<br>FG</div><div class="stat">1.022<br>OG</div><div class="stat srm green">4<br>SRM</div></div></article>

<article class="recipe-card"><div class="photo" role="img" aria-label="Two pints at a bar" style="background:linear-gradient(135deg,#140a06,#7a3414 50%,#d88a3a)"></div><div class="photo-title">Oak Bastard Sweet Mead</div><div class="votes"><div class="vote"><div>♥</div>3</div><div class="vote"><div>✔</div>11</div><div class="vote"><div>★</div>0</div></div><span class="method extract">Extract</span><span class="style">Belgian Tripel</span><p class="desc">Lorem ipsum dolor sit amet, consectetur adipisicing elit.</p><p class="author">Created by <span>Nora Hale</span></p><div class="stats"><div class="stat">2.24%<br>ABV</div><div class="stat">24<br>IBU</div><div class="stat">1.006<br>FG</div><div class="stat">1.022<br>OG</div><div class="stat srm red">4<br>SRM</div></div></article>

<article class="recipe-card"><div class="photo" role="img" aria-label="Assorted drinks in glasses" style="background:linear-gradient(135deg,#2a3a5a,#3a9ad8 45%,#e0a040)"></div><div class="photo-title">Oak Bastard Sweet Mead</div><div class="votes"><div class="vote"><div>♥</div>8</div><div class="vote"><div>✔</div>14</div><div class="vote"><div>★</div>0</div></div><span class="method extract">Extract</span><span class="style">Mild</span><p class="desc">Lorem ipsum dolor sit amet, consectetur adipisicing elit.</p><p class="author">Created by <span>Nora Hale</span></p><div class="stats"><div class="stat">2.24%<br>ABV</div><div class="stat">24<br>IBU</div><div class="stat">1.006<br>FG</div><div class="stat">1.022<br>OG</div><div class="stat srm teal">4<br>SRM</div></div></article>

<article class="recipe-card"><div class="photo" role="img" aria-label="Close-up of amber beer" style="background:linear-gradient(160deg,#c04a12,#e07a24 50%,#8a2c0a)"></div><div class="photo-title">Oak Bastard Sweet Mead</div><div class="votes"><div class="vote"><div>♥</div>7</div><div class="vote"><div>✔</div>50</div><div class="vote"><div>★</div>0</div></div><span class="method extract">Extract</span><span class="style">Belgian Tripel</span><p class="desc">Lorem ipsum dolor sit amet, consectetur adipisicing elit.</p><p class="author">Created by <span>Nora Hale</span></p><div class="stats"><div class="stat">2.24%<br>ABV</div><div class="stat">24<br>IBU</div><div class="stat">1.006<br>FG</div><div class="stat">1.022<br>OG</div><div class="stat srm green">4<br>SRM</div></div></article>

<article class="recipe-card"><div class="photo" role="img" aria-label="Beer glasses with a keg and wheat" style="background:linear-gradient(135deg,#f4efe6,#d89a3e 55%,#7a4718)"></div><div class="photo-title">Oak Bastard Sweet Mead</div><div class="votes"><div class="vote"><div>♥</div>4</div><div class="vote"><div>✔</div>20</div><div class="vote"><div>★</div>0</div></div><span class="method allgrain">AllGrain</span><span class="style">English Cider</span><p class="desc">Lorem ipsum dolor sit amet, consectetur adipisicing elit.</p><p class="author">Created by <span>Nora Hale</span></p><div class="stats"><div class="stat">2.24%<br>ABV</div><div class="stat">24<br>IBU</div><div class="stat">1.006<br>FG</div><div class="stat">1.022<br>OG</div><div class="stat srm blue">4<br>SRM</div></div></article>

<article class="recipe-card"><div class="photo" role="img" aria-label="Row of beer glasses from pale to dark" style="background:linear-gradient(90deg,#2a1408,#b8641e 40%,#d89a3a 60%,#1a0c06)"></div><div class="photo-title">Oak Bastard Sweet Mead</div><div class="votes"><div class="vote"><div>♥</div>2</div><div class="vote"><div>✔</div>8</div><div class="vote"><div>★</div>0</div></div><span class="method partial">PartialMash</span><span class="style">Belgian Tripel</span><p class="desc">Lorem ipsum dolor sit amet, consectetur adipisicing elit.</p><p class="author">Created by <span>Nora Hale</span></p><div class="stats"><div class="stat">2.24%<br>ABV</div><div class="stat">24<br>IBU</div><div class="stat">1.006<br>FG</div><div class="stat">1.022<br>OG</div><div class="stat srm red">4<br>SRM</div></div></article>
</main>

<footer>
  <div class="footer-band"></div>
  <div class="footer-brand"><span class="brand-dot"></span><span class="brand-name">VELVETFINCH</span></div>
  <div class="footer-photo" role="img" aria-label="Group of beer mugs"></div>
  <div class="mailing">
    <h2>JOIN OUR MAILING LIST</h2>
    <p>Sign up for our e-mail list to receive updates</p>
    <div class="email">Your e-mail address<b>JOIN</b></div>
    <span class="connect">Connect with us on</span>
    <div class="social"><i></i><i></i><i></i></div>
  </div>
  <p class="copyright">Copyright © 2013 Velvetfinch. All rights reserved.</p>
</footer>

</body>
</html>
```